Financial Services Consultant needs a business card

We need a business card for a new consulting company based in Melbourne called
"Quelbrook Insights". Tagline is Track, Review, Grow
We would like to see business card designs that are in line with the minimal style of the website www.quelbrook-insights.example
The font I have used on the website is Proxima Nova and would like the same or similar font used on the business card with a minimal design in line with the website Two sided with "QUELBROOK INSIGHTS" TRACK, REVIEW, GROW on one side and name, title and contact details on the otther
Updates

Hi All, thanks for your submissions, much appreciated.

I have recently added some colour to my webiste, it is hex #3a7b74 for those that wish to use it
Thanks

Hi all

thanks very much for your design submissions I am very impressed and they are much appreciated.

Interms of general feedback please find below;

Colour: I am trying to stick to a minimal design and colour scheme for my website which is still under construction, up to 3 colours( www.quelbrook-insights.example) it is currently black and white with a small amount of blue/green but I am open to suggestion/interpretations for a consulting company.

Card: I dont mind if it has rounded edges or straight, I was thinking about using a letterpress card if possible

Detail: the detail on the card will include; Name, Title, Mobile, Personal Email, Business Email,Web,Business Address

Once again thanks for submissions

Industry/Entity Type

Business

```html
<!DOCTYPE html>
<html lang="en">
<head>
<meta charset="utf-8">
<title>Quelbrook Insights — Business Card</title>
<link rel="stylesheet" href="https://fonts.googleapis.com/css2?family=Montserrat:wght@700&family=Open+Sans:wght@400;600;700&display=swap">
<style>
  :root {
    --page-bg: #e4e5ea;
    --card-bg: #ffffff;
    --ink: #111111;
    --ink-soft: #4a4a4a;
    --accent: #3a7b74;
    --card-edge: #2b2b2b;
  }
  * { box-sizing: border-box; margin: 0; padding: 0; }
  html, body {
    width: 1200px; height: 987px; overflow: hidden;
    background: var(--page-bg);
    font-family: "Open Sans", Arial, sans-serif;
  }
  .sheet {
    width: 1200px; height: 987px;
    display: flex; flex-direction: column; align-items: center; justify-content: center;
    gap: 44px;
  }
  .card {
    position: relative;
    width: 760px; height: 434px;
    background: var(--card-bg);
    border: 1px solid var(--card-edge);
    border-radius: 38px;
    overflow: hidden;
  }

  /* Brand side */
  .card--brand {
    display: flex; flex-direction: column; align-items: center; justify-content: center;
  }
  .wordmark {
    font-family: "Montserrat", Arial, sans-serif;
    font-weight: 700;
    color: var(--ink);
    letter-spacing: 0.12em;
    white-space: nowrap;
  }
  .card--brand .wordmark { font-size: 42px; }
  .tagline {
    margin-top: 16px;
    font-size: 22px;
    color: var(--ink-soft);
  }
  .website-spaced {
    margin-top: 26px;
    font-size: 20px;
    letter-spacing: 0.42em;
    color: var(--ink-soft);
  }
  .website-spaced strong { color: var(--ink); font-weight: 700; }

  /* Contact side */
  .accent-bar {
    position: absolute; left: 0; top: 40px;
    width: 26px; height: 50px;
    background: var(--accent);
  }
  .contact {
    position: absolute; left: 58px; top: 40px;
  }
  .person-name {
    font-size: 24px; font-weight: 700; color: var(--ink-soft); line-height: 1.1;
  }
  .person-title {
    font-size: 16px; color: var(--accent); margin-top: 2px;
  }
  .address {
    margin-top: 34px;
    font-size: 17px; line-height: 1.35; color: var(--ink-soft);
    font-style: normal;
  }
  .contact-lines {
    list-style: none;
    position: absolute; left: 40px; top: 200px;
    font-size: 17px; color: var(--ink-soft);
  }
  .contact-lines li { display: flex; align-items: center; gap: 10px; margin-bottom: 10px; }
  .contact-lines svg { width: 15px; height: 15px; flex: none; }
  .card--contact .wordmark {
    position: absolute; right: 48px; bottom: 62px;
    font-size: 32px;
  }
</style>
</head>
<body>
<main class="sheet">
  <section class="card card--brand" aria-label="Card front">
    <h1 class="wordmark">QUELBROOK INSIGHTS</h1>
    <p class="tagline">Track, Review, Grow</p>
    <p class="website-spaced">www.<strong>quelbrook-insights</strong>.example</p>
  </section>

  <section class="card card--contact" aria-label="Card back">
    <div class="accent-bar"></div>
    <div class="contact">
      <p class="person-name">Your Name</p>
      <p class="person-title">Title</p>
      <address class="address">Street Name, City Name<br>State Zip Code</address>
    </div>
    <ul class="contact-lines">
      <li>
        <svg viewBox="0 0 16 16" aria-hidden="true"><circle cx="8" cy="8" r="7" fill="none" stroke="#4a4a4a" stroke-width="1.3"/><path d="M5.5 4.5l1.4 1.4-.8 1c.5 1 1.2 1.7 2.2 2.2l1-.8 1.4 1.4-1 1.2C7.6 10.7 5.3 8.4 4.3 5.5z" fill="#4a4a4a"/></svg>
        <span>123-456-0789</span>
      </li>
      <li>
        <svg viewBox="0 0 16 16" aria-hidden="true"><circle cx="8" cy="8" r="7" fill="none" stroke="#4a4a4a" stroke-width="1.3"/><ellipse cx="8" cy="8" rx="3" ry="7" fill="none" stroke="#4a4a4a" stroke-width="1"/><path d="M1 8h14M2.5 4.5h11M2.5 11.5h11" stroke="#4a4a4a" stroke-width="1"/></svg>
        <span>www.quelbrook-insights.example</span>
      </li>
    </ul>
    <p class="wordmark">QUELBROOK INSIGHTS</p>
  </section>
</main>
</body>
</html>
```